Business Card for Vorla Parts Wholesale supplier

Hi There! I need a new business card for our company. We are specialized in selling Vorla parts, mostly we sell new LCD screens for Zelnar and Drelks. I would like to see that back in the design.

You can find the colors and logo's on our website: www.hartuvo.nl

Industry/Entity Type

Business

Contact Information for Business Card

My Details:
Tobias Lindqvist

Phone: 0031687203316
E-mail: Tobias@hartuvo.nl

Slogan: "Because Quality Matters"

Font styles to use
Sans Serif

Colors

Designer to choose colors to be used in the design.

Requirements
Must have
• A Black backside with the Hartuvo logo on it. The front side should be clean with only my contact details.
• But I'm also open for something really different or awesome!
Nice to have
• Remember that we are in the parts & repairing industry, So i'll be handing those business cards mainly to repair companies. Maybe you can do something with that thought :)

```html
<!DOCTYPE html>
<html lang="en">
<head>
<meta charset="utf-8">
<title>Hartuvo business card</title>
<link href="https://fonts.googleapis.com/css2?family=Exo+2:wght@400;600;700&family=Open+Sans:wght@600&display=swap" rel="stylesheet">
<style>
  :root {
    --orange: #f37021;
    --black: #000000;
    --white: #ffffff;
    --ink: #111111;
    --backdrop: #e9e6e2;
  }
  html, body {
    margin: 0;
    padding: 0;
    overflow: hidden;
  }
  .canvas {
    position: relative;
    width: 1200px;
    height: 987px;
    background: var(--backdrop);
    overflow: hidden;
  }
  .card {
    position: absolute;
    left: 293px;
    width: 615px;
    height: 352px;
    overflow: hidden;
    box-shadow: 0 2px 6px rgba(0,0,0,0.25);
  }
  .card--front { top: 129px; background: var(--black); }
  .card--back  { top: 505px; background: var(--white); }

  .front-panel {
    position: absolute;
    inset: 0;
  }
  .front-brand {
    position: absolute;
    left: 300px;
    top: 150px;
    width: 300px;
    text-align: center;
    font-family: "Exo 2", sans-serif;
    font-weight: 700;
    font-size: 46px;
    color: var(--orange);
    letter-spacing: 0.5px;
  }
  .holder-name {
    position: absolute;
    left: 46px;
    top: 48px;
    margin: 0;
    font-family: "Exo 2", sans-serif;
    font-weight: 700;
    font-size: 21px;
    color: var(--orange);
    letter-spacing: 0.4px;
  }
  .contact-list {
    position: absolute;
    left: 46px;
    top: 240px;
    margin: 0;
    padding: 0;
    list-style: none;
    font-family: "Exo 2", sans-serif;
    font-size: 15px;
    color: var(--white);
  }
  .contact-list li {
    display: flex;
    align-items: center;
    height: 23.5px;
  }
  .contact-icon {
    width: 15px;
    height: 15px;
    margin-right: 10px;
    fill: var(--orange);
  }

  .back-brand {
    position: absolute;
    left: 0;
    right: 0;
    top: 140px;
    display: flex;
    justify-content: center;
    align-items: center;
    gap: 18px;
  }
  .brand-square {
    width: 52px;
    height: 52px;
    background: var(--orange);
  }
  .brand-name {
    font-family: "Exo 2", sans-serif;
    font-weight: 600;
    font-size: 64px;
    line-height: 1;
    color: var(--ink);
  }
  .slogan {
    position: absolute;
    left: 0;
    right: 0;
    top: 281px;
    margin: 0;
    text-align: center;
    font-family: "Open Sans", sans-serif;
    font-weight: 600;
    font-size: 19px;
    color: var(--orange);
  }
</style>
</head>
<body>
<div class="canvas">
  <section class="card card--front">
    <svg class="front-panel" viewBox="0 0 615 352" aria-hidden="true">
      <polygon points="363,0 615,0 615,352 358,352 264,258 264,100" fill="#ffffff"/>
    </svg>
    <div class="front-brand">Hartuvo</div>
    <h1 class="holder-name">Tobias Lindqvist</h1>
    <ul class="contact-list">
      <li>
        <svg class="contact-icon" viewBox="0 0 24 24" aria-hidden="true"><path d="M6.6 10.8a15.1 15.1 0 0 0 6.6 6.6l2.2-2.2a1 1 0 0 1 1-.25 11.4 11.4 0 0 0 3.6.57 1 1 0 0 1 1 1V20a1 1 0 0 1-1 1A17 17 0 0 1 3 4a1 1 0 0 1 1-1h3.5a1 1 0 0 1 1 1c0 1.25.2 2.45.57 3.57a1 1 0 0 1-.25 1z"/></svg>
        0031687203316
      </li>
      <li>
        <svg class="contact-icon" viewBox="0 0 24 24" aria-hidden="true"><path d="M2 5h20v14H2z M2 5l10 8 10-8" fill="none" stroke="#f37021" stroke-width="0"/><path d="M2 6.5V19h20V6.5l-10 7.5z"/><path d="M2 5h20l-10 7.5z"/></svg>
        Tobias@hartuvo.nl
      </li>
      <li>
        <svg class="contact-icon" viewBox="0 0 24 24" aria-hidden="true"><circle cx="12" cy="12" r="10"/><path d="M12 2v20M2 12h20M5 6.5c4 2 10 2 14 0M5 17.5c4-2 10-2 14 0" stroke="#000" stroke-width="1.3" fill="none"/></svg>
        www.hartuvo.nl
      </li>
    </ul>
  </section>

  <section class="card card--back">
    <div class="back-brand">
      <span class="brand-square"></span>
      <span class="brand-name">hartuvo</span>
    </div>
    <p class="slogan">Because Quality Matters</p>
  </section>
</div>
</body>
</html>
```